Awesome Digital Ad Design – Vexora Adloop

I am going to be setting up a Vexora Adloop ad campaign I need creatives for.

Several sizes are needed in the end, however, please submit your design concept in the following 2 sizes to start:
Medium rectangle: 300X250
Leaderboard: 728X90

Original artwork/design files and images used expected upon payment and as part of the final delivery.

Ads should match our company brand and the information on this webpage: http://www.harbelstandwork.com/real-estate-marketing/
SEE MORE INSTRUCTIONS IN ATTACHED WORD DOC

Target Market(s)

Business-To-Business Audience –Real Estate Company Executives (Presidents/VPs/Owners/CEOs/Sales Managers).

Industry/Entity Type

Real Estate

Font styles to use
Sans Serif

Requirements
Must have
• Copy should be minimal words, billboard like. Please use real photos/images that would appeal to real estate high-level decision-maker executives.
Should not have
• No cartoons or graphics

```html
<!DOCTYPE html>
<html lang="en">
<head>
<meta charset="utf-8">
<title>Harbel Standwork – Display Ads</title>
<link href="https://fonts.googleapis.com/css2?family=Oswald:wght@500;600&family=Roboto:wght@500;700&family=Roboto+Condensed:wght@700&display=swap" rel="stylesheet">
<style>
  :root {
    --stage: #2e2e2e;
    --maroon: #6c2b3b;
    --steel: #527590;
    --orange: #e8621f;
    --orange-edge: #f08a4e;
    --white: #ffffff;
    --tan: #cbb27c;
    --ink: #333333;
  }
  * { margin: 0; padding: 0; box-sizing: border-box; }
  html, body { width: 1200px; height: 1200px; overflow: hidden; background: var(--stage); }
  .canvas { position: relative; width: 1200px; height: 1200px; background: var(--stage); }

  /* Medium rectangle */
  .ad-rect { position: absolute; left: 82px; top: 74px; width: 1036px; height: 864px; overflow: hidden; }
  .scene-photo {
    position: absolute; inset: 0;
    background: linear-gradient(180deg, #dfe4e8 0%, #cfd7dd 40%, #b9c6b4 72%, #9fb98a 80%, #e6e2dd 92%, #d8d4cf 100%);
  }
  .agent-photo {
    position: absolute; left: 530px; top: 0; width: 506px; height: 750px;
    background: linear-gradient(180deg, #cdd3d8 0%, #b89a88 30%, #5e4550 55%, #4a3840 100%);
  }
  .brand-box {
    position: absolute; left: 48px; top: 0; width: 214px; height: 206px;
    background: var(--white); display: flex; align-items: center; justify-content: center; text-align: center;
  }
  .brand-name { font-family: "Roboto", sans-serif; font-weight: 500; color: var(--ink); font-size: 26px; line-height: 1.15; }
  .band-headline { position: absolute; left: 0; top: 264px; width: 634px; height: 183px; background: var(--maroon); }
  .band-offer { position: absolute; left: 0; top: 467px; width: 534px; height: 156px; background: var(--steel); }
  .headline, .offer { position: absolute; left: 50px; font-family: "Oswald", sans-serif; font-weight: 500; color: var(--white); text-transform: uppercase; line-height: 1; white-space: nowrap; }
  .headline { top: 20px; }
  .headline .line-1 { font-size: 60px; letter-spacing: -1px; display: block; }
  .headline .line-2 { font-size: 80px; letter-spacing: -1px; display: block; margin-top: 6px; }
  .offer { top: 12px; }
  .offer .line-1 { font-size: 50px; letter-spacing: -1px; display: block; }
  .offer .line-2 { font-size: 68px; letter-spacing: -1px; display: block; margin-top: 8px; }
  .cta {
    position: absolute; display: flex; align-items: center; justify-content: center; gap: 50px;
    background: var(--orange); border: 3px solid var(--orange-edge); border-radius: 10px;
    color: var(--white); font-family: "Roboto", sans-serif; font-weight: 700; text-transform: uppercase; white-space: nowrap;
  }
  .ad-rect .cta { left: 189px; top: 726px; width: 653px; height: 109px; font-size: 72px; }
  .cta svg { display: block; }

  /* Leaderboard */
  .ad-board { position: absolute; left: 82px; top: 1010px; width: 1035px; height: 127px; overflow: hidden; background: var(--white); }
  .board-photo {
    position: absolute; right: 0; top: 0; width: 260px; height: 127px;
    background: linear-gradient(180deg, #cfd6dc 0%, #8d7a7f 50%, #4d3a44 100%);
  }
  .board-band { position: absolute; inset: 0; }
  .board-brand { position: absolute; left: 8px; top: 0; width: 160px; height: 127px; display: flex; align-items: center; justify-content: center; text-align: center; }
  .board-brand .brand-name { font-size: 16px; }
  .board-copy {
    position: absolute; top: 14px; white-space: nowrap;
    font-family: "Roboto Condensed", sans-serif; font-weight: 700; font-size: 31px; line-height: 33px;
    text-transform: uppercase; color: var(--white);
  }
  .board-copy .accent { color: var(--tan); }
  .board-copy-left { left: 130px; width: 232px; text-align: right; }
  .board-copy-right { left: 418px; width: 250px; text-align: left; }
  .board-divider { position: absolute; left: 389px; top: 0; height: 127px; border-left: 1px dashed rgba(255,255,255,0.5); }
  .ad-board .cta { left: 684px; top: 42px; width: 204px; height: 44px; font-size: 23px; gap: 14px; border-radius: 5px; border-width: 2px; }
</style>
</head>
<body>
<main class="canvas">

  <section class="ad-rect" aria-label="Medium rectangle ad">
    <div class="scene-photo" role="img" aria-label="Photo of a house exterior with front lawn"></div>
    <div class="agent-photo" role="img" aria-label="Smiling real estate agent holding a SOLD sign"></div>
    <div class="brand-box"><span class="brand-name">Harbel<br>Standwork</span></div>
    <div class="band-headline">
      <h1 class="headline"><span class="line-1">Client Follow-Up</span><span class="line-2">Made Simple</span></h1>
    </div>
    <div class="band-offer">
      <p class="offer"><span class="line-1">Virtually no cost to</span><span class="line-2">Your company!</span></p>
    </div>
    <a class="cta">Learn More
      <svg width="68" height="68" viewBox="0 0 68 68" aria-hidden="true">
        <circle cx="34" cy="34" r="30" fill="none" stroke="#ffffff" stroke-width="7"/>
        <path d="M20 28 H34 V18 L50 34 L34 50 V40 H20 Z" fill="#ffffff"/>
      </svg>
    </a>
  </section>

  <section class="ad-board" aria-label="Leaderboard ad">
    <div class="board-photo" role="img" aria-label="Real estate agent holding a SOLD sign in front of a house"></div>
    <svg class="board-band" width="1035" height="127" viewBox="0 0 1035 127" aria-hidden="true">
      <polygon points="182,0 875,0 787,127 110,127" fill="#6c2b3b"/>
    </svg>
    <div class="board-brand"><span class="brand-name">Harbel<br>Standwork</span></div>
    <p class="board-copy board-copy-left">Client<br>Follow-Up<br><span class="accent">Made Simple</span></p>
    <div class="board-divider"></div>
    <p class="board-copy board-copy-right">Virtually<br>No cost to<br><span class="accent">Your company!</span></p>
    <a class="cta">Learn More
      <svg width="26" height="26" viewBox="0 0 68 68" aria-hidden="true">
        <circle cx="34" cy="34" r="30" fill="none" stroke="#ffffff" stroke-width="7"/>
        <path d="M20 28 H34 V18 L50 34 L34 50 V40 H20 Z" fill="#ffffff"/>
      </svg>
    </a>
  </section>

</main>
</body>
</html>
```